Quillmarsh Property Solutions need a business card design

Hello guys. We would need a business card design asap please.
We are a start up property investment business based in London UK specialised in buying, selling, managing and letting properties and helping distressed property owners.
The name of our Business is Quillmarsh, the logo symbolises the four fundamental elements of the world (earth, air, fire and water) and so it stands for strength, stability, longevity.
We would like the business card to communicate professionalism and reliability. Many many thanks indeed for your work.

Details:

1.) Rosalind Updike
Property Investor
Mobile: +44(0)7700123456
Email: rosalind.quillmarsh@mailbox-example.com

2.) Dominic Updike
Property Investor
Mobile: +44(0)7700987654
Email: dominic.quillmarsh@mailbox-example.com

```html
<!DOCTYPE html>
<html lang="en">
<head>
<meta charset="utf-8">
<title>Quillmarsh Property Solutions — Business Card</title>
<link rel="stylesheet" href="https://fonts.googleapis.com/css2?family=Open+Sans:wght@400;700&display=swap">
<style>
  :root {
    --stage: #e3e4e6;
    --card-dark: #000000;
    --card-light: #ffffff;
    --ink-light: #ffffff;
    --ink-dark: #111111;
    --band-red: #e3202b;
    --band-green: #1f9a3a;
    --band-blue: #2f63c9;
    --mark-grey: #8a8f96;
  }
  * { box-sizing: border-box; margin: 0; padding: 0; }
  html, body {
    width: 1200px; height: 800px; overflow: hidden;
    background: var(--stage);
    font-family: "Open Sans", Arial, sans-serif;
  }
  .sheet {
    width: 1200px; height: 800px;
    display: flex; align-items: center; justify-content: center; gap: 60px;
  }
  .card {
    position: relative; width: 525px; height: 300px; overflow: hidden;
    box-shadow: 0 6px 18px rgba(0,0,0,0.12);
  }
  /* Front */
  .card-front { background: var(--card-dark); color: var(--ink-light); }
  .band { position: absolute; left: 0; width: 100%; height: 22px; display: flex; }
  .band-top { top: 0; }
  .band-bottom { bottom: 0; }
  .band span { flex: 1; }
  .red { background: var(--band-red); }
  .green { background: var(--band-green); }
  .blue { background: var(--band-blue); }
  .front-lockup {
    position: absolute; left: 50%; top: 50%; transform: translate(-50%, -50%);
    display: flex; align-items: center; gap: 18px; white-space: nowrap;
  }
  .mark-square { width: 46px; height: 46px; background: var(--mark-grey); flex: none; }
  .brand-name {
    font-weight: 400; color: var(--ink-light); font-size: 23px;
    line-height: 1.15; letter-spacing: 1px; text-transform: uppercase;
  }
  /* Back */
  .card-back { background: var(--card-light); color: var(--ink-dark); }
  .back-lockup {
    position: absolute; left: 60px; top: 62px;
    display: flex; align-items: center; gap: 12px; white-space: nowrap;
  }
  .back-lockup .mark-square { width: 32px; height: 32px; }
  .back-lockup .brand-name { color: var(--ink-dark); font-size: 14px; letter-spacing: 0.5px; }
  .contact {
    position: absolute; left: 250px; top: 150px; width: 250px;
    font-size: 11.5px; line-height: 1.45; white-space: nowrap;
  }
  .contact-name { font-size: 19px; line-height: 1.3; margin-bottom: 2px; }
</style>
</head>
<body>
<main class="sheet">
  <section class="card card-front" aria-label="Card front">
    <div class="band band-top">
      <span class="green"></span><span class="red"></span><span class="blue"></span><span class="green"></span><span class="red"></span>
    </div>
    <div class="front-lockup">
      <div class="mark-square"></div>
      <p class="brand-name">Quillmarsh<br>Property Solutions</p>
    </div>
    <div class="band band-bottom">
      <span class="red"></span><span class="green"></span><span class="blue"></span><span class="red"></span><span class="green"></span>
    </div>
  </section>

  <section class="card card-back" aria-label="Card back">
    <div class="back-lockup">
      <div class="mark-square"></div>
      <p class="brand-name">Quillmarsh<br>Property Solutions</p>
    </div>
    <div class="contact">
      <p class="contact-name">Rosalind Updike</p>
      <p>Property Investor</p>
      <p>Mobile: +44(0)7700123456</p>
      <p>Email: rosalind.quillmarsh@mailbox-example.com</p>
      <p>London, United Kingdom</p>
    </div>
  </section>
</main>
</body>
</html>
```